Flat Belly Design Graphics for Social

I want to create 9 social media graphics (new Instagram size 4:5 (1080 x 1350 pixels) focusing on our Flat Belly Graphics, using the pics attached. Use the attached pics, NO RANDOM STOCK PHOTOGRAPHY. For the color scheme of the graphics, the color palette is attached. YOU MUST POST ALL 9 GRAPHICS IN ONE ENTRY.
Using the 3 titles below, create one set of graphics. 1) with all text, then for the others, use the pictures as detailed below in IMPORTANT:
1. Ten-Week Bright Morning Reboot
2. The Quick Garden Kitchen Menu Guide
3. Studio Habits for Lasting Energy Past Midlife - Zero Gym Needed
IMPORTANT:
Only use RK Pic 1 and RK Pic 2 with the title, Ten-Week Bright Morning Reboot
Only use meal plan1 and meal plan2 pics with the title, Quick Garden Kitchen Menu Guide
Only use studio habits 1 and studio habits 2 pics with the title, Studio Habits for Lasting Energy Past Midlife - Zero Gym Needed
women over 40

```html
<!DOCTYPE html>
<html lang="en">
<head>
<meta charset="UTF-8">
<title>Ten-Week Bright Morning Reboot</title>
<link rel="stylesheet" href="https://fonts.googleapis.com/css2?family=Antonio:wght@100;600&family=Archivo+Black&family=Montserrat:wght@400;500&display=swap">
<style>
  :root {
    --blush: #f6d9df;
    --rose: #e399ae;
    --rose-line: #e3a0b3;
    --teal: #2f4a48;
    --cream: #fbf6ee;
    --ink: #1f2a2a;
  }
  html, body {
    margin: 0;
    padding: 0;
    overflow: hidden;
    background: var(--blush);
  }
  .poster {
    position: relative;
    width: 960px;
    height: 1200px;
    overflow: hidden;
    background: var(--blush);
  }
  .poster svg {
    position: absolute;
    inset: 0;
  }
  .kicker { font-family: "Archivo Black", sans-serif; fill: var(--cream); }
  .headline-light { font-family: "Antonio", sans-serif; font-weight: 100; fill: var(--rose); }
  .headline-bold { font-family: "Antonio", sans-serif; font-weight: 600; fill: var(--teal); }
  .subline { font-family: "Montserrat", sans-serif; font-weight: 500; fill: var(--blush); }
  .site-url { font-family: "Montserrat", sans-serif; font-weight: 400; fill: var(--ink); letter-spacing: 2.5px; }
</style>
</head>
<body>
<main class="poster">
  <svg width="960" height="1200" viewBox="0 0 960 1200" xmlns="http://www.w3.org/2000/svg">
    <defs>
      <linearGradient id="orbFade" x1="0" y1="0" x2="1" y2="1">
        <stop offset="0.15" stop-color="#2f4f4c"/>
        <stop offset="0.8" stop-color="#d8c5c9"/>
      </linearGradient>
      <linearGradient id="pillFade" x1="0" y1="0" x2="1" y2="0">
        <stop offset="0" stop-color="#f6d9df"/>
        <stop offset="1" stop-color="#e399ae"/>
      </linearGradient>
      <linearGradient id="photoTone" x1="0" y1="0" x2="0" y2="1">
        <stop offset="0" stop-color="#3a2a24"/>
        <stop offset="0.3" stop-color="#c99578"/>
        <stop offset="0.6" stop-color="#9ec7dc"/>
        <stop offset="0.75" stop-color="#c99578"/>
        <stop offset="1" stop-color="#3f5f8a"/>
      </linearGradient>
    </defs>

    <!-- top rule and orb -->
    <line class="top-rule" x1="0" y1="87" x2="742" y2="87" stroke="var(--rose-line)" stroke-width="2"/>
    <circle class="corner-orb" cx="889" cy="98" r="147" fill="url(#orbFade)"/>

    <!-- photo area -->
    <rect class="hero-photo" role="img" aria-label="Photo of two smiling women, one whispering to the other, in a light blue crop top and denim jeans" x="0" y="178" width="409" height="915" fill="url(#photoTone)" opacity="0.85"/>

    <!-- side stripes -->
    <g class="side-stripes" stroke="var(--rose-line)" stroke-width="1.2">
      <line x1="904" y1="367" x2="960" y2="367"/><line x1="904" y1="377" x2="960" y2="377"/><line x1="904" y1="387" x2="960" y2="387"/><line x1="904" y1="397" x2="960" y2="397"/><line x1="904" y1="407" x2="960" y2="407"/><line x1="904" y1="417" x2="960" y2="417"/><line x1="904" y1="427" x2="960" y2="427"/><line x1="904" y1="437" x2="960" y2="437"/><line x1="904" y1="447" x2="960" y2="447"/><line x1="904" y1="457" x2="960" y2="457"/><line x1="904" y1="467" x2="960" y2="467"/><line x1="904" y1="477" x2="960" y2="477"/><line x1="904" y1="487" x2="960" y2="487"/><line x1="904" y1="497" x2="960" y2="497"/><line x1="904" y1="507" x2="960" y2="507"/><line x1="904" y1="517" x2="960" y2="517"/><line x1="904" y1="527" x2="960" y2="527"/><line x1="904" y1="537" x2="960" y2="537"/><line x1="904" y1="547" x2="960" y2="547"/><line x1="904" y1="557" x2="960" y2="557"/><line x1="904" y1="567" x2="960" y2="567"/><line x1="904" y1="577" x2="960" y2="577"/><line x1="904" y1="587" x2="960" y2="587"/><line x1="904" y1="597" x2="960" y2="597"/><line x1="904" y1="607" x2="960" y2="607"/><line x1="904" y1="617" x2="960" y2="617"/><line x1="904" y1="627" x2="960" y2="627"/><line x1="904" y1="637" x2="960" y2="637"/><line x1="904" y1="647" x2="960" y2="647"/><line x1="904" y1="657" x2="960" y2="657"/><line x1="904" y1="667" x2="960" y2="667"/>
      <line x1="904" y1="716" x2="960" y2="716"/><line x1="904" y1="726" x2="960" y2="726"/><line x1="904" y1="736" x2="960" y2="736"/><line x1="904" y1="746" x2="960" y2="746"/><line x1="904" y1="756" x2="960" y2="756"/><line x1="904" y1="766" x2="960" y2="766"/><line x1="904" y1="776" x2="960" y2="776"/><line x1="904" y1="786" x2="960" y2="786"/><line x1="904" y1="796" x2="960" y2="796"/><line x1="904" y1="806" x2="960" y2="806"/><line x1="904" y1="816" x2="960" y2="816"/><line x1="904" y1="826" x2="960" y2="826"/><line x1="904" y1="836" x2="960" y2="836"/><line x1="904" y1="846" x2="960" y2="846"/><line x1="904" y1="856" x2="960" y2="856"/><line x1="904" y1="866" x2="960" y2="866"/><line x1="904" y1="876" x2="960" y2="876"/><line x1="904" y1="886" x2="960" y2="886"/><line x1="904" y1="896" x2="960" y2="896"/><line x1="904" y1="906" x2="960" y2="906"/><line x1="904" y1="916" x2="960" y2="916"/><line x1="904" y1="926" x2="960" y2="926"/><line x1="904" y1="936" x2="960" y2="936"/><line x1="904" y1="946" x2="960" y2="946"/><line x1="904" y1="956" x2="960" y2="956"/><line x1="904" y1="966" x2="960" y2="966"/><line x1="904" y1="976" x2="960" y2="976"/><line x1="904" y1="986" x2="960" y2="986"/><line x1="904" y1="996" x2="960" y2="996"/><line x1="904" y1="1006" x2="960" y2="1006"/><line x1="904" y1="1016" x2="960" y2="1016"/>
    </g>

    <!-- title block -->
    <g class="title-block">
      <rect class="kicker-box" x="593" y="418" width="280" height="53" fill="var(--teal)"/>
      <text class="kicker" x="633" y="461" font-size="36" textLength="240" lengthAdjust="spacingAndGlyphs">TEN-WEEK</text>

      <text class="headline-light" x="873" y="640" font-size="188" text-anchor="end" textLength="330" lengthAdjust="spacingAndGlyphs">BRIGHT</text>

      <text class="headline-bold" x="873" y="809" font-size="188" text-anchor="end" textLength="489" lengthAdjust="spacingAndGlyphs">MORNING</text>

      <rect class="subline-band" x="384" y="828" width="489" height="56" fill="var(--rose)"/>
      <text class="subline" x="873" y="880" font-size="56" text-anchor="end">Reboot</text>
    </g>

    <!-- footer -->
    <path class="url-pill" d="M0 1093 H470 A34.5 34.5 0 0 1 470 1162 H0 Z" fill="url(#pillFade)"/>
    <text class="site-url" x="220" y="1135" font-size="23">www.loremipsum</text>

    <g class="pointer-arrow" stroke="var(--rose-line)" stroke-width="1.6" fill="none">
      <line x1="530" y1="1128" x2="960" y2="1128"/>
      <polyline points="538,1119 529,1128 538,1137"/>
    </g>
  </svg>
</main>
</body>
</html>
```